Sparrow Haulage needs a business card design.

Design a double-sided business card for new freight business. On the front, would like to see our logo along with the following info:

Martin Obuya
CEO/FOUNDER
555-206-7142
martinobuya@sparrow-haulage.example

On the reverse side, we would like to use the graphic image of our logo only without the Sparrow Haulage name.

```html
<!DOCTYPE html>
<html lang="en">
<head>
<meta charset="utf-8">
<title>Sparrow Haulage – Business Card</title>
<link href="https://fonts.googleapis.com/css2?family=Arimo:wght@400;700&display=swap" rel="stylesheet">
<style>
  :root {
    --backdrop: #a9a9a9;
    --navy: #000050;
    --navy-soft: #0b0f63;
    --red: #c00000;
    --ink: #2a2a2a;
    --rule: #8a8a8a;
    --paper: #ffffff;
  }
  html, body {
    margin: 0;
    width: 1200px;
    height: 1200px;
    overflow: hidden;
    background: var(--backdrop);
    font-family: "Arimo", Arial, sans-serif;
  }
  .canvas {
    position: relative;
    width: 1200px;
    height: 1200px;
  }
  .card {
    position: absolute;
    top: 303px;
    width: 368px;
    height: 594px;
  }
  .card-back {
    left: 201px;
    background: var(--navy);
  }
  .back-mark {
    position: absolute;
    left: 114px;
    top: 217px;
    width: 140px;
    height: 140px;
    background: var(--navy-soft);
  }
  .card-front {
    left: 599px;
    width: 364px;
    background: var(--paper);
    text-align: center;
  }
  .brand {
    position: absolute;
    top: 462px;
    top: 160px;
    left: 0;
    right: 0;
    display: flex;
    align-items: center;
    justify-content: center;
    gap: 12px;
  }
  .brand-square {
    width: 34px;
    height: 34px;
    background: var(--red);
  }
  .brand-name {
    font-weight: 700;
    font-size: 25px;
    letter-spacing: 2px;
    color: var(--navy);
    line-height: 1;
  }
  .person {
    position: absolute;
    top: 376px;
    left: 0;
    right: 0;
  }
  .person-name {
    margin: 0;
    font-weight: 700;
    font-size: 22px;
    line-height: 1;
  }
  .person-name .given { color: var(--navy); }
  .person-name .family { color: var(--red); }
  .person-role {
    margin: 6px 0 0;
    font-size: 17px;
    color: var(--ink);
    line-height: 1;
  }
  .icon-row {
    position: absolute;
    top: 439px;
    left: 0;
    right: 0;
    display: flex;
    align-items: center;
    justify-content: center;
    gap: 4px;
  }
  .icon-row .rule {
    width: 52px;
    height: 1px;
    background: var(--rule);
    margin: 0 3px;
  }
  .icon {
    width: 25px;
    height: 25px;
    background: var(--red);
    border-radius: 3px;
    display: flex;
    align-items: center;
    justify-content: center;
  }
  .contact {
    position: absolute;
    top: 478px;
    left: 0;
    right: 0;
    font-size: 16px;
    color: var(--ink);
    line-height: 22px;
  }
  .contact p { margin: 0; }
  .web .navy { color: var(--navy); }
  .web .red { color: var(--red); }
</style>
</head>
<body>
<div class="canvas">
  <section class="card card-back" aria-label="Card reverse">
    <div class="back-mark" role="img" aria-label="Embossed brand symbol area"></div>
  </section>

  <section class="card card-front" aria-label="Card front">
    <div class="brand">
      <span class="brand-square"></span>
      <span class="brand-name">SPARROW HAULAGE</span>
    </div>

    <div class="person">
      <h1 class="person-name"><span class="given">MARTIN</span> <span class="family">OBUYA</span></h1>
      <p class="person-role">CEO/FOUNDER</p>
    </div>

    <div class="icon-row">
      <span class="rule"></span>
      <span class="icon" aria-label="Phone">
        <svg width="15" height="13" viewBox="0 0 15 13"><path d="M1 4 Q7.5 -1 14 4 L12 6 L10 5 L10 3.5 Q7.5 2.5 5 3.5 L5 5 L3 6 Z" fill="#fff"/><rect x="3" y="7" width="9" height="5" rx="1" fill="#fff"/></svg>
      </span>
      <span class="icon" aria-label="Email">
        <svg width="15" height="11" viewBox="0 0 15 11"><rect x="0.5" y="0.5" width="14" height="10" fill="none" stroke="#fff"/><path d="M0.5 0.5 L7.5 6 L14.5 0.5 M0.5 10.5 L5.5 5 M14.5 10.5 L9.5 5" fill="none" stroke="#fff"/></svg>
      </span>
      <span class="icon" aria-label="Website">
        <svg width="15" height="15" viewBox="0 0 15 15"><circle cx="7.5" cy="7.5" r="6.5" fill="#fff"/><circle cx="7.5" cy="7.5" r="3" fill="var(--red)"/></svg>
      </span>
      <span class="rule"></span>
    </div>

    <div class="contact">
      <p class="phone">555-206-7142</p>
      <p class="email">martinobuya@sparrow-haulage.example</p>
      <p class="web">www.<span class="navy">sparrow</span>-<span class="red">haulage</span>.example</p>
    </div>
  </section>
</div>
</body>
</html>
```